Business card design for a dynamic IT consulting company

We need a business card design for a young firm, specialized in the Telecommunications/Consulting industry. The name of the company is Quindor and Partners Business Consulting Ltd. (Short name: Quindor and Partnes)
Quindor = solve read reverse, so we aim to be uncomplicated and solution-oriented. The small pipe in our logo is also related to the word solve. So we need a new business card design, which is simple, eye catching and something non traditional (I would probably prefer a square shaped design rather than a rectangle, but open for suggestions). Attached our logo.

Target Market(s)

Usually our customers are Tier1 Telecoms providers (Q-Netra, Palorix, etc) and their executives.

Industry/Entity Type

Business

Contact Information for Business Card

Name: Bence Tolnavari
Email: b.tolnavari@quindor.hu
Web: www.quindor.hu
Mobile: +36 30 518 2769
Title: Managing Director

Optional:
Company name: Quindor and Partners Ltd.
Address: 1087 Budapest, Tolvenka str. 28/C, Hungary

Font styles to use
Other font styles liked:
• helveticaneue_medium, Prime Regular are used now.

Colors

Designer to choose colors to be used in the design.

Requirements
Must have
• I would like to have a 2 sided design.
Nice to have
• I thought if we make the logo a bit bigger (without the company name), that could go to the back with the company name below. I though, if the pipe in the logo is somehow touchable on the business card, would be nice and unique.

```html
<!DOCTYPE html>
<html lang="en">
<head>
<meta charset="utf-8">
<title>Quindor &amp; Partners – Business Card</title>
<link rel="stylesheet" href="https://fonts.googleapis.com/css2?family=Exo+2:wght@400;500&family=Work+Sans:wght@400&display=swap">
<style>
  :root {
    --stage: #1c1c1e;
    --paper: #ffffff;
    --magenta: #bb3090;
    --blue: #1a8fd6;
    --ink: #4a4a4c;
    --ink-soft: #555558;
  }
  * { margin: 0; padding: 0; box-sizing: border-box; }
  html, body {
    width: 1200px; height: 897px; overflow: hidden;
    background: var(--stage);
  }
  .card {
    position: absolute;
    left: 304px;
    width: 594px;
    height: 338px;
    border-radius: 22px;
    overflow: hidden;
  }
  .card--front { top: 92px; background: var(--paper); }
  .card--back  { top: 470px; background: var(--magenta); }

  .brand {
    position: absolute;
    display: flex; align-items: center; gap: 12px;
    font-family: "Exo 2", sans-serif; font-weight: 400;
    white-space: nowrap;
  }
  .brand__mark { display: block; }
  .card--front .brand { left: 38px; top: 42px; font-size: 38px; color: var(--ink-soft); }
  .card--front .brand__mark { width: 14px; height: 14px; background: var(--magenta); }
  .card--back .brand { left: 0; right: 0; top: 138px; justify-content: center; font-size: 56px; color: #fff; }
  .card--back .brand__mark { width: 20px; height: 20px; background: #fff; }

  .person__name {
    position: absolute; left: 42px; top: 168px;
    font-family: "Exo 2", sans-serif; font-weight: 400;
    font-size: 22px; letter-spacing: 0.5px; color: var(--blue);
    text-transform: uppercase;
  }
  .person__title {
    position: absolute; left: 42px; top: 197px;
    font-family: "Work Sans", sans-serif; font-size: 14px; color: var(--ink);
  }
  .divider {
    position: absolute; left: 44px; top: 231px; width: 506px; height: 2px;
    background: var(--magenta);
  }
  .contacts {
    position: absolute; left: 48px; top: 250px; list-style: none;
    font-family: "Work Sans", sans-serif; font-size: 13.5px; color: var(--ink);
  }
  .contacts li { display: flex; align-items: center; gap: 10px; height: 19px; }
  .contacts svg { width: 12px; height: 12px; fill: var(--blue); }
  .company {
    position: absolute; right: 44px; top: 254px; text-align: right;
    font-family: "Work Sans", sans-serif; font-size: 13.5px; line-height: 17px; color: var(--ink);
  }
  .company__name {
    font-family: "Exo 2", sans-serif; font-weight: 500;
    font-size: 15px; color: var(--blue); text-transform: uppercase;
    margin-bottom: 2px;
  }
  .footer-band { position: absolute; left: 0; bottom: 0; width: 594px; height: 28px; }

  .back__web {
    position: absolute; left: 0; right: 0; top: 296px; text-align: center;
    font-family: "Work Sans", sans-serif; font-size: 15px; letter-spacing: 2.5px; color: #fff;
  }
</style>
</head>
<body>
  <section class="card card--front" aria-label="Business card front">
    <div class="brand"><span class="brand__mark"></span>Quindor &amp; Partners</div>

    <h1 class="person__name">Bence Tolnavari</h1>
    <p class="person__title">Managing Director</p>
    <div class="divider"></div>

    <ul class="contacts">
      <li>
        <svg viewBox="0 0 24 24"><path d="M6.6 10.8a15.1 15.1 0 0 0 6.6 6.6l2.2-2.2a1 1 0 0 1 1-.25 11.4 11.4 0 0 0 3.6.57 1 1 0 0 1 1 1V20a1 1 0 0 1-1 1A17 17 0 0 1 3 4a1 1 0 0 1 1-1h3.5a1 1 0 0 1 1 1c0 1.25.2 2.45.57 3.57a1 1 0 0 1-.25 1z"/></svg>
        +36 30 518 2769
      </li>
      <li>
        <svg viewBox="0 0 24 24"><path d="M2 5h20v2l-10 6L2 7z"/><path d="M2 9l10 6 10-6v10H2z"/></svg>
        b.tolnavari@quindor.hu
      </li>
      <li>
        <svg viewBox="0 0 24 24"><path d="M12 2a10 10 0 1 0 0 20 10 10 0 0 0 0-20zm6.9 6h-2.9a15.6 15.6 0 0 0-1.4-3.6A8 8 0 0 1 18.9 8zM12 4c.8 1.2 1.5 2.5 1.9 4h-3.8c.4-1.5 1.1-2.8 1.9-4zM4.3 14a8 8 0 0 1 0-4h3.3a16 16 0 0 0 0 4zm.8 2h2.9c.3 1.3.8 2.5 1.4 3.6A8 8 0 0 1 5.1 16zM8 8H5.1a8 8 0 0 1 4.3-3.6C8.8 5.5 8.3 6.7 8 8zm4 12c-.8-1.2-1.5-2.5-1.9-4h3.8c-.4 1.5-1.1 2.8-1.9 4zm2.3-6H9.7a14 14 0 0 1 0-4h4.6a14 14 0 0 1 0 4zm.3 5.6c.6-1.1 1.1-2.3 1.4-3.6h2.9a8 8 0 0 1-4.3 3.6zm1.8-5.6a16 16 0 0 0 0-4h3.3a8 8 0 0 1 0 4z"/></svg>
        www.quindor.hu
      </li>
    </ul>

    <address class="company" style="font-style:normal">
      <div class="company__name">Quindor and Partners Ltd.</div>
      1087 Budapest, Tolvenka<br>str. 28/C, Hungary
    </address>

    <svg class="footer-band" viewBox="0 0 594 28" preserveAspectRatio="none" aria-hidden="true">
      <path d="M0 18 H594 V28 H0 Z" fill="var(--magenta)"/>
      <path d="M0 11 H340 Q352 11 362 6 Q374 0 396 0 H594 V18 H0 Z" fill="var(--magenta)"/>
      <path d="M0 11 H342 Q334 16 322 16 H0 Z" fill="var(--blue)"/>
    </svg>
  </section>

  <section class="card card--back" aria-label="Business card back">
    <div class="brand"><span class="brand__mark"></span>Quindor &amp; Partners</div>
    <p class="back__web">www.quindor.hu</p>
  </section>
</body>
</html>
```